Nutritional & Gastrointestinal Health Consulting Service-Website design

We need a website design for a new health consulting service called "Bright Vale" based in Perth, Australia.

We will be providing consulting services in the areas of:
1) Nutrition and Diet
2) Gastrointestinal Health (which means stomach & digestive system related health)

These consulting services will be provided by an Accredited Dietitian and a Paediatric Gastroenterologist.

We are open to creative ideas in terms of design, layout, fonts and colours. We also would love to see images of nature in the backdrop with families (adults with kids) having a good time, fresh fruits and vegetables displayed in a farmer's market or supermarket. 2 or 3 images should be sufficient. We would also definitely want our logo somewhere in the main page of website. The logo file is also attached. Please have a look at a website's design that we really liked. We would love to see designs inspired by that style. The website details are in the in the "nice to have priorities" section of this project brief.

We also would be looking at website designers with software coding skills so that if we like the design we can go ahead with the next step of coding.

The website design should communicate the purpose of the website and at the same time be simple, elegant and unique/eye-catching.

We look forward to receiving creative ideas for our website from you all. Good luck!

More details have been added to our project- for example: Logo, fonts style, must haves etc etc. Please view the updated project brief. Looking forward to receiving your fantastic ideas for our website. Thanking you

Hi, I have updated the colour preference. Will add the content preferences tomorrow. thanks

Hello all, I have now added a LOT more content to what we want in our website. It is very much in detail, so please carefully have a read through the entire project brief. If you have any questions write back to me and I will try to respond as quickly as I can. Last few days were busy so couldn't respond quickly to all of you who had send me designs/queries/questions. Thank you for your patience. I look forward to receiving fantastic designs from you all. Good Luck :-)

Target Market(s)

Adults based in western speaking countries aged 18 to 60 years

Industry/Entity Type

Software

Font styles to use
Sans Serif
Script

Colors
faa54b
acd036

Requirements
Must have
• The website must have the MAIN logo file attached. I have attached 3 files: 1) MAIN logo; 2) supplementary logo A ; 3) supplementary logo B

I have selected 2 colours from the colour scheme (see below)-(as the colour of our logo is that).
However we would also like to see LIGHT CHOCOLATE BROWN or CHOCOLATE BROWN colour used as the background colour of the website
Preferred WEBSITE CONTENT:
1) HOME PAGE:
Content required=
--Company Logo
--Dr Dorian Pelham
Paediatric Gastroenterologist & Hepatologist
-Marla Pelham.
Dietitian & Nutritionist
--Website Menu (either listed horizontally or vertically):
Once clicked on each name:

Under each of the Website Menu items we want the following Headings to be added

2) ABOUT US page:
Sub-heading under this: Qualification, Skills, Special Interest

3) SERVICES
DORIAN'S PAGE: Individual Consultation, Endoscopy procedures
Individual Consultation, Group Based Services, Food Diary, Food & Symptom Diary

4) FEES & REBATE: Content as below:
Please Note: Payment of full fees is required at the time of consultation and procedures. 48 hours notice is required for cancellation of appointments/non-attendance. Failure to provide this may result in a fee being incurred. Please call reception to find out the amount of fee charged for cancellation of appointments/non-attendance.
headings are:
Paediatric Gastroenterology:
Dorian's pge
Individual Consultation - Initial (upto 30 mins):
Review Consultation (upto 15 mins):
Endoscopy procedures - No Gap fees charged. Fees will be billed directly to Vitacover. If any queries, please contact reception.

marla's pge
sub heading:
Individual Consultation - Initial (upto 45 mins):
Individual Consultation - Review (upto 30 mins):

Concession-Individual Consultation -Initial (upto 45 mins):
Concession-Individual Consultation - Review (upto 30 mins):
Please Note: Concession applies for health care card holders & pensioners

Group Based Services: Pricing subject to the type of service provided. Please contact us for an obligation free quote.
Education Topics Include:
- Paediatric Nutrition (Introducing Solids, Fussy Eating, Healthy Eating)
- Pregnancy Nutrition, Gestational Diabetes, Breastfeeding/Lactation Nutrition
- Healthy Eating, Supermarket Shopping Tips, Nutrition Label Reading Tips, Healthier
sub heading under nutrition & diet:
-Vitacover:
--A rebate of $52.95 is available from Vitacover if an EPC ( Enhanced Primary Care)/Chronic Disease Management (CDM) plan is issued by your GP.
--All mandatory paperwork needs to be available at the time of making your appointment for your eligibility.
-Private Health Fund:
--Most private health funds provide rebate on dietetic appointments. However the rebate amount depends on your level of cover. Thus, please contact your health fund to determine your entitled rebate.
-RSB: Approved provider for RSB services

6) FOR DOCTORS: Bright Vale Paediatric Gastroenterologist Referral Form
Bright Vale Dietitian Referral form
7) LOCATIONS & CONTACT

Paediatric Gastroenterology & Hepatology Service
Suite 46
Holy Lantern Bramcote Medical Centre
17 Colin Ferris Pde,
MURDOCH, WA 6150
P: (08) 9422 5061
F: (08) 9422 3094

Nutrition & Diet Service
Suite 46
17 Colin Ferris Pde,
MURDOCH, WA 6150
P: (08) 9422 5061
F: (08) 9422 3094

Tolland Medical Centre
58-60 Karrigan Parkway,
MANDURAH, WA 6210
P: (08) 9647 2283
F: (08) 96724419
www.tmcexample.com.au

This page should have a webform that has following titles:
-Your Name
-Your Email
-Your Phone
-Message

8) NEWS & BLOG
Nice to have
• We liked the design style of the websites below:
https://www.vendoraplex.example/

http://qoravelt.example/

But feel free to use your creativity too
Should not have
• Please do not use any body building or muscle building images

```html
<!DOCTYPE html>
<html lang="en">
<head>
<meta charset="utf-8">
<title>About Me – Dr Dorian Pelham | Bright Vale</title>
<link href="https://fonts.googleapis.com/css2?family=Open+Sans:wght@300;400;700&display=swap" rel="stylesheet">
<style>
  :root {
    --orange: #f9a44b;
    --orange-deep: #e09341;
    --tab: #e8954a;
    --white: #ffffff;
    --ink: #3d2a17;
    --ink-soft: #4a321b;
    --rule: rgba(255,255,255,0.75);
    --photo-light: #ece4d8;
    --photo-mid: #c8b8a4;
    --photo-dark: #6f7f95;
  }
  * { margin: 0; padding: 0; box-sizing: border-box; }
  html, body { width: 1200px; height: 1181px; overflow: hidden; }
  body {
    background: var(--orange);
    font-family: "Open Sans", Arial, sans-serif;
    position: relative;
    color: var(--ink);
  }
  .brand {
    position: absolute; top: 26px; left: 52px;
    display: flex; align-items: center; gap: 8px;
    color: var(--white); font-weight: 700; font-size: 18px; line-height: 24px;
  }
  .brand-dot {
    width: 14px; height: 14px; border-radius: 50%; background: var(--white);
  }
  .side-tab {
    position: absolute; top: 89px; width: 47px; height: 47px;
    background: var(--tab);
    display: flex; align-items: center; justify-content: center;
  }
  .side-tab--menu { left: 0; }
  .side-tab--close { right: 0; color: var(--white); font-size: 13px; }
  .page-title {
    position: absolute; top: 88px; left: 0; width: 100%;
    text-align: center; color: var(--white);
    font-weight: 700; font-size: 16px; letter-spacing: 0.3px;
  }
  .title-rule {
    position: absolute; top: 169px; left: 52px; width: 1094px;
    border-top: 1px dashed var(--rule);
  }
  .name-frame {
    position: absolute; top: 216px; left: 441px; width: 319px; height: 112px;
    border: 1px solid var(--white);
    color: var(--white); text-align: center;
    padding-top: 17px; line-height: 37px; font-size: 36px;
  }
  .name-frame .first { font-weight: 300; display: block; }
  .name-frame .last { font-weight: 700; display: block; }
  .specialty {
    position: absolute; top: 343px; left: 0; width: 100%;
    text-align: center; font-weight: 300; font-size: 20px; color: var(--ink);
  }
  .intro {
    position: absolute; top: 389px; left: 330px; width: 540px;
    text-align: center; font-family: Arial, Helvetica, sans-serif;
    font-size: 13.2px; line-height: 18.75px; color: var(--ink-soft);
  }
  .intro .highlight { color: var(--white); }
  .intro strong { font-weight: 700; color: var(--ink); }
  .portrait {
    position: absolute; top: 520px; left: 333px; width: 534px; height: 357px;
    background: linear-gradient(100deg, var(--photo-mid) 0%, var(--photo-light) 40%, var(--photo-dark) 70%, var(--photo-light) 100%);
  }
  .callout {
    position: absolute; top: 914px; left: 52px; width: 1096px; height: 220px;
    background: var(--orange-deep); border-radius: 3px; text-align: center;
  }
  .callout h2 {
    margin-top: 50px; font-weight: 300; font-size: 31px; color: var(--white); line-height: 36px;
  }
  .callout p { font-weight: 300; font-size: 20px; color: var(--ink); line-height: 30px; }
  .ask-button {
    display: inline-block; margin-top: 12px; width: 178px; height: 42px;
    background: var(--white); border-bottom: 4px solid #e2e2e2;
    font-size: 17px; font-weight: 300; color: var(--ink); line-height: 40px;
  }
</style>
</head>
<body>
  <div class="brand"><span class="brand-dot"></span><span>Bright Vale</span></div>

  <div class="side-tab side-tab--menu" aria-label="Menu">
    <svg width="12" height="10" viewBox="0 0 12 10"><rect y="0" width="12" height="2" fill="#fff"/><rect y="4" width="12" height="2" fill="#fff"/><rect y="8" width="12" height="2" fill="#fff"/></svg>
  </div>
  <div class="side-tab side-tab--close" aria-label="Close">×</div>

  <h1 class="page-title">ABOUT ME</h1>
  <div class="title-rule"></div>

  <div class="name-frame">
    <span class="first">DR DORIAN</span>
    <span class="last">PELHAM</span>
  </div>

  <h3 class="specialty">PAEDIATRIC GASTROENTELOGIST HEPATOLOGIST</h3>

  <p class="intro">Lorem ipsum dolor sit amet, consectetuer <span class="highlight">adipiscing elit</span>, sed diam nonummy nibh euismod tincidunt ut laoreet dolore magna aliquam erat volutpat. Ut wisi enim ad minim veniam, quis nostrud exerci tation ullamcorper suscipit lobortis nisl ut aliquip ex ea <strong>commodo consequat</strong>. Duis autem vel eum iriure dolor in hendrerit in vulputate velit esse molestie consequat.</p>

  <div class="portrait" role="img" aria-label="Photo of a smiling doctor in a white coat talking with an older patient"></div>

  <section class="callout">
    <h2>PAEDIATRIC GASTROENTELOGIST HEPATOLOGIST</h2>
    <p>Lorem ipsum dolor sit amet, consectetuer adipiscing elit, sed diam nonummy nibh euismod</p>
    <span class="ask-button">Ask your Question</span>
  </section>
</body>
</html>
```